Business Card - high end, modern health care

Hey designers!

We need a double sided business card for the boutique, cutting edge physical therapy rehabilitation centre in Sydney's Northern Beaches.

With the most qualified physios in the area The Harbourview Motion Clinic does what other physiotherapy practices do not, we take our time with our patients giving them longer appointments, better physios and therefor faster results!

We guarantee that the service people receive at THMC will be unparalleled.

Hence we need a business card to reflect our modern, boutique, high end service. The final design needs to reflect that we are in a class of our own yet with the feel of beachside retreat.

Below I have attached our logo in both blue on white and white on blue. The exact colour is;
and the font that we have used in our logo is Tex Gyre Aventador.

I like the idea of the blue as the main colour as it is more eye catching and our signage onto the main road will be in this blue and in the interest of consistency across marketing the blue needs to be a part of the design. However I would appreciate a few designs onto a wooden background as this is a visual theme within the fitout of the practice.

The design needs to be of standard size (91x55mm).

Target Market(s)

We target people who have an end outcome in mind and those who have had poor experiences with other providers and ensure that everyone gets the care that they deserve with a premium service that is tailored to the individuals circumstances. As a premium service, the target market is highly educated, business and tech savvy with the additional target market of elderly people who have self funded their retirement and see value in paying for the best ongoing rehabilitation to maintain independence.

Industry/Entity Type

Physical Therapy

Contact Information for Business Card

Name, designation( Titled Musculoskeletal Physiotherapist... there will also be those in the company that have multiple designations ie 5 or 6 words long), phone number, email, facebook, instagram, address

Font styles to use
Sans Serif

Colors

Designer to choose colors to be used in the design.

Requirements
Must have
• Front - The logo as large as possible, blue or wooden theme, and all of the important details.
• Back - A blank space/lines on which to write appointment times (no "Appointment, date, time" etc.)
Nice to have
• facebook url
• logos for facebook and instagram
• Mini logos for the phone and email?

```html
<!DOCTYPE html>
<html lang="en">
<head>
<meta charset="utf-8">
<title>The Harbourview Motion Clinic – Business Card</title>
<link href="https://fonts.googleapis.com/css2?family=Raleway:wght@400;500;700&display=swap" rel="stylesheet">
<style>
  :root {
    --brand-blue: #0d55a5;
    --paper: #ffffff;
    --ink: #1a1a1a;
    --rule: #222222;
    --muted-rule: #9a9a9a;
    --backdrop: #e9e7e4;
    --social-blue: #1d8fd8;
    --social-pink: #e0508f;
  }
  * { box-sizing: border-box; margin: 0; padding: 0; }
  html, body {
    width: 1200px; height: 1200px; overflow: hidden;
    background: var(--backdrop);
    font-family: "Raleway", sans-serif;
    color: var(--ink);
  }
  .canvas {
    position: relative; width: 1200px; height: 1200px;
  }
  .card {
    position: absolute; left: 190px; width: 820px; height: 496px;
    box-shadow: 0 10px 28px rgba(0,0,0,0.18);
  }
  /* Front */
  .card-front {
    top: 70px; background: var(--brand-blue);
    display: flex; flex-direction: column; align-items: center; justify-content: center;
    gap: 26px; color: var(--paper);
  }
  .front-mark {
    width: 150px; height: 150px; border-radius: 50%; background: var(--paper);
  }
  .front-name {
    font-weight: 700; font-size: 30px; letter-spacing: 0.08em;
    text-transform: uppercase; text-align: center; line-height: 1.3;
  }
  /* Back */
  .card-back {
    top: 634px; background: var(--paper);
  }
  .rule {
    position: absolute; height: 1.5px; background: var(--rule);
  }
  .rule-top { top: 96px; left: 250px; right: 40px; }
  .rule-mid { top: 236px; left: 40px; right: 120px; }
  .rule-appointment {
    position: absolute; top: 440px; left: 60px; right: 60px;
    border-top: 1.5px dashed var(--muted-rule);
  }
  .brand {
    position: absolute; top: 128px; left: 40px;
    display: flex; align-items: center; gap: 12px;
  }
  .brand-dot {
    width: 48px; height: 48px; border-radius: 50%; background: var(--brand-blue); flex: none;
  }
  .brand-name {
    font-weight: 700; font-size: 17px; line-height: 1.25; letter-spacing: 0.06em;
    text-transform: uppercase; color: var(--brand-blue);
  }
  .person {
    position: absolute; top: 124px; left: 440px;
  }
  .person-name {
    font-weight: 400; font-size: 36px; line-height: 1.1;
  }
  .person-name .accent { color: var(--brand-blue); }
  .person-title {
    font-size: 16px; font-weight: 500; margin-top: 8px;
  }
  .contacts {
    position: absolute; top: 262px; left: 300px;
    list-style: none; display: flex; flex-direction: column; gap: 14px;
  }
  .contact {
    display: flex; align-items: center; gap: 16px; font-size: 22px;
  }
  .contact svg { width: 26px; height: 26px; flex: none; }
  .handle-dot {
    width: 26px; height: 26px; border-radius: 50%; flex: none;
  }
  .handle-dot.handle-primary { background: var(--social-blue); }
  .handle-dot.handle-secondary { background: var(--social-pink); }
</style>
</head>
<body>
<main class="canvas">

  <section class="card card-front" aria-label="Card front">
    <div class="front-mark"></div>
    <p class="front-name">The Harbourview<br>Motion Clinic</p>
  </section>

  <section class="card card-back" aria-label="Card back">
    <div class="rule rule-top"></div>

    <div class="brand">
      <div class="brand-dot"></div>
      <p class="brand-name">The Harbourview<br>Motion Clinic</p>
    </div>

    <div class="person">
      <p class="person-name">Name of <span class="accent">Person</span></p>
      <p class="person-title">Designation</p>
    </div>

    <div class="rule rule-mid"></div>

    <ul class="contacts">
      <li class="contact">
        <svg viewBox="0 0 24 24" aria-hidden="true">
          <circle cx="12" cy="12" r="10.5" fill="none" stroke="#1a1a1a" stroke-width="2"/>
          <path d="M9 7.5c-.8.6-1.2 1.5-1 2.6.5 2.6 2.3 4.6 4.8 5.8 1 .4 2 .2 2.7-.6l.4-.5-2-1.6-1 .8c-1.2-.6-2.2-1.6-2.8-2.8l.8-1-1.5-2.1z" fill="#1a1a1a"/>
        </svg>
        <span>555.014.2290</span>
      </li>
      <li class="contact">
        <svg viewBox="0 0 24 24" aria-hidden="true">
          <rect x="2" y="5" width="20" height="14" fill="#1a1a1a"/>
          <path d="M2.5 5.5 12 13l9.5-7.5" fill="none" stroke="#fff" stroke-width="1.6"/>
        </svg>
        <span>hello@harbourviewmotion.com</span>
      </li>
      <li class="contact">
        <span class="handle-dot handle-primary"></span>
        <span>/harbourviewmotion</span>
      </li>
      <li class="contact">
        <span class="handle-dot handle-secondary"></span>
        <span>@harbourview.motion</span>
      </li>
    </ul>

    <div class="rule-appointment"></div>
  </section>

</main>
</body>
</html>
```